New business card/stationary for a consulting company

I am looking for a clean and very professional looking business card for my consulting company as well as corresponding stationary. I am uploading our logo. I like simple and powerful for the feel. No graphics but I am open on everything else. Below is my contact information but would like the final to be in a version I can add my employees information into and print. Thank you.

Daniel Whitcombe
dan@ferncliffadvisory.com
2870 North 9th Avenue, Summit Floor, Elm Ridge, Illinois 60531
www.ferncliffadvisory.com

Industry/Entity Type

Consulting

Contact Information for Business Card

Daniel Whitcombe
dan@ferncliffadvisory.com
www.ferncliffadvisory.com

Font styles to use
Serif
Sans Serif

Requirements
Must have
• Our logo and the business card details.
Nice to have
• our website www.ferncliffadvisory.com

```html
<!DOCTYPE html>
<html lang="en">
<head>
<meta charset="utf-8">
<title>Ferncliff Advisory — Business Card</title>
<link rel="stylesheet" href="https://fonts.googleapis.com/css2?family=Questrial&family=Crimson+Pro:wght@400;700&display=swap">
<style>
  :root {
    --navy: #06065f;
    --paper: #f7f7f8;
    --ink: #121212;
    --backdrop: #e3e3e5;
    --white: #ffffff;
  }
  * { margin: 0; padding: 0; box-sizing: border-box; }
  html, body { width: 1200px; height: 968px; overflow: hidden; }
  body {
    background: var(--backdrop);
    position: relative;
  }
  .card {
    position: absolute;
    left: 250px;
    width: 700px;
    height: 400px;
    overflow: hidden;
    box-shadow: 0 2px 6px rgba(0,0,0,0.12);
  }
  .card--front { top: 64px; background: var(--navy); color: var(--white); }
  .card--back { top: 504px; background: var(--paper); color: var(--ink); }

  /* front */
  .brand-mark {
    position: absolute;
    left: 328px; top: 92px;
    width: 44px; height: 44px;
    background: var(--white);
  }
  .brand-name {
    position: absolute;
    left: 0; right: 0; top: 178px;
    text-align: center;
    font-family: "Questrial", sans-serif;
    font-size: 40px;
    letter-spacing: 2px;
    line-height: 1;
  }
  .rule { position: absolute; height: 2px; background: var(--white); }
  .rule--upper { left: 596px; right: 0; top: 196px; width: auto; }
  .rule--url { left: 140px; width: 168px; top: 274px; }
  .rule--base { left: 0; right: 0; top: 340px; }
  .brand-url {
    position: absolute;
    left: 322px; top: 262px;
    font-family: "Crimson Pro", serif;
    font-size: 19px;
    letter-spacing: 0.5px;
  }

  /* back */
  .person-name {
    position: absolute;
    left: 232px; top: 126px;
    font-family: "Crimson Pro", serif;
    font-weight: 700;
    font-size: 34px;
    letter-spacing: 0.6px;
  }
  .contact-list {
    position: absolute;
    left: 252px; top: 172px;
    list-style: none;
    font-family: "Crimson Pro", serif;
    font-size: 19px;
    line-height: 26px;
  }
  .contact-bands { position: absolute; left: 0; top: 184px; }
  .band {
    position: absolute;
    left: 0;
    width: 238px;
    height: 22px;
    background: var(--navy);
  }
  .band svg { position: absolute; right: 6px; top: 3px; }
</style>
</head>
<body>

<section class="card card--front" aria-label="Card front">
  <div class="brand-mark"></div>
  <div class="brand-name">FERNCLIFF ADVISORY</div>
  <div class="rule rule--upper"></div>
  <div class="rule rule--url"></div>
  <div class="brand-url">www.ferncliffadvisory.com</div>
  <div class="rule rule--base"></div>
</section>

<section class="card card--back" aria-label="Card back">
  <div class="person-name">Daniel Whitcombe</div>

  <div class="contact-bands">
    <div class="band" style="top:0">
      <svg width="16" height="16" viewBox="0 0 16 16" aria-hidden="true">
        <rect x="1.5" y="3.5" width="13" height="9" fill="none" stroke="#fff" stroke-width="1.4"/>
        <path d="M1.5 3.5 L8 9 L14.5 3.5" fill="none" stroke="#fff" stroke-width="1.4"/>
      </svg>
    </div>
    <div class="band" style="top:28px">
      <svg width="16" height="16" viewBox="0 0 16 16" aria-hidden="true">
        <circle cx="8" cy="8" r="6.5" fill="#fff"/>
        <path d="M4 5 Q6 6 5 8 Q7 10 6 12 M10 4 Q9 6 11 7 Q12 9 11 11" fill="none" stroke="#06065f" stroke-width="1.3"/>
      </svg>
    </div>
    <div class="band" style="top:56px">
      <svg width="16" height="16" viewBox="0 0 16 16" aria-hidden="true">
        <path d="M8 15 C4 10 3 8 3 6 A5 5 0 0 1 13 6 C13 8 12 10 8 15 Z" fill="#fff"/>
        <circle cx="8" cy="6" r="2" fill="#06065f"/>
      </svg>
    </div>
  </div>

  <ul class="contact-list">
    <li>dan@ferncliffadvisory.com</li>
    <li>www.ferncliffadvisory.com</li>
    <li>2870 North 9th Avenue, Summit Floor,</li>
    <li>Elm Ridge, Illinois 60531</li>
  </ul>
</section>

</body>
</html>
```